Business Card Design Project

Business Card
We are rebranding with a new logo
Industry/Entity Type
Business
Contact Information for Business Card
Dennis Morvale +61 487215963 dennis@quorv.com.au P.O. Box 872 Fernlow QLD 4309
Requirements
Must have
- Logo

```html
<!DOCTYPE html>
<html lang="en">
<head>
<meta charset="utf-8">
<title>Quorv International – Business Card</title>
<link rel="stylesheet" href="https://fonts.googleapis.com/css2?family=Exo+2:wght@400;500;600&display=swap">
<style>
  :root {
    --page-bg: #e6e6e6;
    --card-white: #ffffff;
    --brand-blue: #0897cf;
    --brand-orange: #ea6a1d;
    --text-light: #ffffff;
  }
  * { margin: 0; padding: 0; box-sizing: border-box; }
  html, body {
    width: 1200px;
    height: 898px;
    overflow: hidden;
    background: var(--page-bg);
    font-family: "Exo 2", sans-serif;
  }
  .card {
    position: absolute;
    left: 180px;
    top: 209px;
    width: 840px;
    height: 480px;
    background: var(--card-white);
    box-shadow: 0 6px 18px rgba(0,0,0,0.18);
    overflow: hidden;
  }
  .card__panel {
    position: absolute;
    inset: 0;
    width: 840px;
    height: 480px;
  }
  .card__panel .accent { fill: var(--brand-orange); }
  .card__panel .band { fill: var(--brand-blue); }
  .contact {
    position: absolute;
    left: 88px;
    top: 150px;
    color: var(--text-light);
  }
  .contact__name {
    font-size: 22px;
    font-weight: 500;
    letter-spacing: 1.5px;
    line-height: 1.05;
    text-transform: uppercase;
    margin-bottom: 28px;
  }
  .contact__line {
    font-size: 17px;
    font-weight: 400;
    letter-spacing: 0.6px;
    line-height: 1.35;
  }
  .contact__group + .contact__group { margin-top: 26px; }
  .brand {
    position: absolute;
    left: 560px;
    top: 150px;
    width: 240px;
    text-align: center;
    color: var(--brand-blue);
    font-weight: 600;
  }
  .brand__name {
    font-size: 64px;
    line-height: 1;
    letter-spacing: 1px;
  }
  .brand__sub {
    font-size: 20px;
    letter-spacing: 6px;
    text-transform: uppercase;
    margin-top: 10px;
  }
</style>
</head>
<body>
  <div class="card">
    <svg class="card__panel" viewBox="0 0 840 480" aria-hidden="true">
      <path class="accent" d="M0 0 L368 0 C388 200 480 380 572 480 L0 480 Z"/>
      <path class="band" d="M0 0 L360 0 C380 200 470 380 562 480 L0 480 Z"/>
    </svg>

    <div class="contact">
      <p class="contact__name">Dennis<br>Morvale</p>
      <div class="contact__group">
        <p class="contact__line">Cell: +61 487215963</p>
        <p class="contact__line">Email: dennis@quorv.com.au</p>
      </div>
      <div class="contact__group">
        <p class="contact__line">P.O. Box 872</p>
        <p class="contact__line">Fernlow QLD 4309</p>
      </div>
    </div>

    <div class="brand">
      <p class="brand__name">Quorv</p>
      <p class="brand__sub">International</p>
    </div>
  </div>
</body>
</html>
```